Building Design company needing a letterhead

We need a letter head for our Building Design company to send letters etc. to our clients, consultants, councils etc. We would like to see our logo used and company colours. I have attached our style guide and an example of our current letterheads. Top left we would like our logo, top right we would like the company details and at the footer we would like some sort of image/design etc. that suits our brand. I like the Tarrow Design letterhead attached.

Target Market(s)

Professionals, Councils, Consultants, Mums & Dads

Industry/Entity Type

Architecture

Other font styles liked:
• refer the design style guide

Colors
f37122
000000
1b1b1b

Requirements
Must have
• Must have the minimum of a logo, company details and footer
Nice to have
• An image/design made for the footer that would suite our brand and website at www.corvanplans.com.au. Also it would be nice to include the KMEOT logo somewhere perhaps included in the footer.
Should not have
• Large images in the header. I just want the logo and company details.

```html
<!DOCTYPE html>
<html lang="en">
<head>
<meta charset="utf-8">
<title>Corvan Design – Letterhead</title>
<link href="https://fonts.googleapis.com/css2?family=Open+Sans:wght@400;600&family=Roboto+Condensed:wght@400&display=swap" rel="stylesheet">
<style>
  :root {
    --brand-orange: #f37122;
    --brand-black: #000000;
    --ink: #1b1b1b;
    --paper: #f8f8f8;
    --backdrop: #e4e2de;
    --white: #ffffff;
  }
  html, body {
    margin: 0;
    padding: 0;
    width: 1189px;
    height: 1200px;
    overflow: hidden;
    background: var(--backdrop);
  }
  .canvas {
    position: relative;
    width: 1189px;
    height: 1200px;
  }
  .letterhead {
    position: absolute;
    left: 138px;
    top: 9px;
    width: 912px;
    height: 1181px;
    background: var(--paper);
    box-shadow: 0 4px 18px rgba(0,0,0,0.18);
    overflow: hidden;
  }
  .letterhead__frame {
    position: absolute;
    inset: 0;
    width: 912px;
    height: 1181px;
  }
  .brand {
    position: absolute;
    left: 43px;
    top: 52px;
    display: flex;
    align-items: center;
    gap: 22px;
  }
  .brand__square {
    width: 82px;
    height: 82px;
    background: var(--brand-orange);
  }
  .brand__name {
    font-family: "Open Sans", sans-serif;
    font-weight: 600;
    color: var(--white);
    font-size: 42px;
    line-height: 46px;
    letter-spacing: 3px;
    text-transform: uppercase;
    margin: 0;
  }
  .contact {
    position: absolute;
    right: 46px;
    top: 108px;
    margin: 0;
    font-family: "Open Sans", sans-serif;
    font-size: 14px;
    line-height: 17px;
    color: var(--ink);
    text-align: right;
    font-style: normal;
  }
  .letter-body {
    font-family: "Roboto Condensed", sans-serif;
    font-size: 17px;
    line-height: 27px;
    color: var(--ink);
  }
  .letter-body p {
    position: absolute;
    left: 142px;
    width: 676px;
    margin: 0;
    hyphens: auto;
  }
  .letter-body .para-1 { top: 302px; }
  .letter-body .para-2 { top: 517px; }
  .letter-body .para-3 { top: 758px; }
  .member-badge {
    position: absolute;
    left: 776px;
    top: 1032px;
    width: 74px;
    text-align: center;
  }
  .member-badge__square {
    width: 62px;
    height: 62px;
    margin: 0 auto 8px;
    border: 3px solid var(--brand-orange);
    box-sizing: border-box;
  }
  .member-badge__name {
    font-family: "Open Sans", sans-serif;
    font-weight: 600;
    font-size: 16px;
    letter-spacing: 1px;
    color: var(--brand-orange);
  }
</style>
</head>
<body>
<div class="canvas">
  <section class="letterhead" lang="en">
    <svg class="letterhead__frame" viewBox="0 0 912 1181" aria-hidden="true">
      <rect width="912" height="1181" fill="var(--brand-black)"/>
      <path d="M0,408 C150,210 440,85 700,90 C800,92 870,100 912,109 L912,866 C780,1040 500,1172 219,1181 C120,1181 40,1172 0,1164 Z" fill="var(--paper)"/>
    </svg>

    <header class="brand">
      <div class="brand__square"></div>
      <p class="brand__name">Corvan<br>Design</p>
    </header>

    <address class="contact">
      admin@corvanplans.com.au<br>
      www.corvanplans.com.au<br>
      Unit 3/22 Harbour Rise Westport WA 6190<br>
      PO Box 5187 Westport North WA 6190<br>
      PH (08) 6500 0142&nbsp;&nbsp;&nbsp; ABN 41 302 118 764
    </address>

    <main class="letter-body">
      <p class="para-1">Lorem Ipsum is simply dummy text of the printing and typesetting industry. Lorem Ipsum has been the industry’s standard dummy text ever since the 1500s, when an unknown printer took a galley of type and scrambled it to make a type specimen book. It has survived not only five centuries, but also the leap into electronic typesetting, remaining essentially unchanged. It was popularised in the 1960s with the release of Transfera sheets containing Lorem Ipsum passages, and more recently with desktop publishing software like PageComposer including versions of Lorem Ipsum.</p>
      <p class="para-2">It is a long established fact that a reader will be distracted by the readable content of a page when looking at its layout. The point of using Lorem Ipsum is that it has a more-or-less normal distribution of letters, as opposed to using ’Content here, content here’, making it look like readable English. Many desktop publishing packages and web page editors now use Lorem Ipsum as their default model text, and a search for ’lorem ipsum’ will uncover many web sites still in their infancy. Various versions have evolved over the years, sometimes by accident, sometimes on purpose (injected humour and the like).</p>
      <p class="para-3">Contrary to popular belief, Lorem Ipsum is not simply random text. It has roots in a piece of classical Latin literature from 45 BC, making it over 2000 years old. Edwin Harlow, a Latin professor at Marlowe College in Vermont, looked up one of the more obscure Latin words, consectetur, from a Lorem Ipsum passage, and going through the cites of the word in classical literature, discovered the undoubtable source. Lorem Ipsum comes from sections 1.10.32 and 1.10.33 of "de Finibus Bonorum et Malorum" structures, to generate Lorem Ipsum which looks reasonable. The generated Lorem Ipsum is therefore always free from repetition, injected humour, or non-characteristic words etc.</p>
    </main>

    <footer class="member-badge">
      <div class="member-badge__square"></div>
      <div class="member-badge__name">KMEOT</div>
    </footer>
  </section>
</div>
</body>
</html>
```